World Wide News and Current Affairs website

We intends to start up a new website which deals on New and Current Affairs.
Attention Designers,
We want a home page design for this project. Our business is based in the United States. Our goal is to become a well known brand.
The website would consist of a category for News, Business and Tech.
The theme should be beautiful and attention seeking. The website would take bulk of it's news from the US, and Europe.
Designers can get inspiration from already existing new websites such as PWJ, KLV, DASKOLM.
All designs should be clean and easy to navigate.

```html
<!DOCTYPE html>
<html lang="en">
<head>
<meta charset="utf-8">
<title>Harlow Daily — Home</title>
<link href="https://fonts.googleapis.com/css2?family=Open+Sans:wght@400;600;700&display=swap" rel="stylesheet">
<style>
:root{
  --brand-dark:#0b5275;
  --brand-mid:#0f6a92;
  --cyan:#27b3d9;
  --cyan-dark:#1a9dc4;
  --ink:#2a2a2a;
  --text:#555;
  --muted:#8a8a8a;
  --line:#e2e2e2;
  --page:#ffffff;
  --tag:#2b2b2b;
  --footer:#232323;
  --footer-bottom:#141414;
  --fans:#2f5c97;
  --followers:#2faae0;
  --subs:#f1893a;
}
*{box-sizing:border-box;margin:0;padding:0}
html,body{width:1200px;height:2594px;overflow:hidden}
body{position:relative;background:var(--page);font-family:"Open Sans",Arial,sans-serif;color:var(--text)}
.abs{position:absolute}

/* header */
.topbar{left:0;top:0;width:1200px;height:86px;background:linear-gradient(180deg,var(--brand-mid),var(--brand-dark))}
.logo{left:99px;top:18px;font-size:34px;font-weight:700;color:#fff;letter-spacing:.2px}
.account{right:232px;top:31px;color:#fff;font-size:17px;letter-spacing:.5px;white-space:nowrap}
.account span{margin:0 10px}
.social-mini{right:93px;top:30px;display:flex;gap:11px}
.social-mini i{display:block;width:22px;height:22px;background:#fff;border-radius:3px}
.nav{left:0;top:86px;width:1200px;height:52px;background:linear-gradient(180deg,#3cc3e6,var(--cyan-dark))}
.nav ul{position:absolute;left:92px;top:0;width:1020px;height:52px;list-style:none}
.nav li{position:absolute;top:0;width:140px;height:52px;line-height:52px;color:#fff;font-size:15px;text-transform:uppercase;text-align:center;white-space:nowrap}
.nav li.active{background:#2b2b2b;width:105px}

/* hero */
.hero{left:88px;top:164px;width:1024px;height:516px;border:1px solid var(--line);box-shadow:0 2px 6px rgba(0,0,0,.15);
  background:linear-gradient(100deg,#f6f8fb 0%,#eef2f6 40%,#f3e3d8 62%,#d9dfe7 100%);overflow:hidden}
.hero .photo{position:absolute;right:110px;top:0;width:420px;height:516px;background:linear-gradient(180deg,#efd3bd,#a7b6c8 50%,#4c6380);opacity:.8;
  -webkit-mask-image:linear-gradient(90deg,transparent,#000 30%);mask-image:linear-gradient(90deg,transparent,#000 30%)}
.hero-title{left:84px;top:228px;font-size:56px;color:var(--cyan);font-weight:400;letter-spacing:1px}
.hero-sub{left:86px;top:292px;font-size:28px;color:#2d3a4a}
.hero-arrows{left:86px;top:348px;display:flex;gap:6px}
.hero-arrows span{width:28px;height:28px;border-radius:50%;background:#7b7b7b;display:flex;align-items:center;justify-content:center}

/* section headings */
.heading{font-size:20px;font-weight:400;color:var(--ink);text-transform:uppercase}
.rule{height:3px;background:var(--cyan)}
.panel{border:1px solid var(--line);box-shadow:0 1px 4px rgba(0,0,0,.12);background:#fff}

/* cards */
.card{position:absolute;width:311px;height:283px;overflow:hidden}
.card .shade{position:absolute;left:0;right:0;bottom:0;height:120px;background:linear-gradient(180deg,rgba(0,0,0,0),rgba(0,0,0,.7))}
.card h3{position:absolute;left:22px;bottom:52px;color:#fff;font-weight:400;font-size:19px;white-space:nowrap}
.card .meta{position:absolute;left:22px;right:22px;bottom:16px;display:flex;justify-content:space-between;align-items:center;color:#ddd;font-size:11px}
.meta .icons{display:flex;gap:12px}
.ico{width:14px;height:14px;display:inline-block}
.badge{position:absolute;right:0;top:0;width:83px;height:83px;background:var(--cyan);color:#fff;text-align:center;padding-top:12px}
.badge b{display:block;font-size:30px;font-weight:400;line-height:32px}
.badge small{font-size:12px}

.pop-item{position:absolute;left:16px;display:flex;gap:22px}
.thumb{width:73px;height:73px;flex:none}
.pop-item p,.list-item p{font-size:12.5px;color:#444;line-height:19px;width:185px}
.mini-icons{display:flex;gap:12px;margin-top:6px}
.mini-icons svg{width:13px;height:13px}

.biz{position:absolute;top:30px;width:197px}
.biz .img{width:197px;height:138px}
.biz p{margin-top:24px;font-size:13px;line-height:20px;color:#444}
.biz .date{margin-top:36px;font-size:12px;color:#666;display:flex;gap:10px;align-items:center}

.tag{position:absolute;height:34px;line-height:34px;background:var(--tag);color:#fff;font-size:13px;text-align:center;white-space:nowrap}
.tag.on{background:var(--cyan)}

.count{position:absolute;top:2130px;width:97px;height:114px;color:#fff;text-align:center;font-size:13px;line-height:16px;padding-top:20px}
.count i{display:block;width:30px;height:30px;border-radius:50%;background:rgba(255,255,255,.25);margin:0 auto 10px}

/* footer */
.footer{left:0;top:2287px;width:1200px;height:237px;background:var(--footer);color:#ddd}
.footer h4{position:absolute;top:33px;font-size:17px;font-weight:400;color:#fff;text-transform:uppercase}
.footer p{font-size:12.5px;line-height:20px}
.email{position:absolute;left:93px;top:122px;width:215px;height:30px;background:#eee;color:#888;font-size:12px;line-height:30px;padding-left:12px}
.subscribe{position:absolute;left:93px;top:166px;width:96px;height:28px;background:var(--cyan);color:#fff;font-size:12px;line-height:28px;text-align:center;border-radius:2px}
.follow{position:absolute;left:683px;display:flex;align-items:center;gap:18px;font-size:12.5px}
.follow i{width:32px;height:32px;border:1px solid #aaa;border-radius:50%;display:block}
.foot-logo{left:899px;top:114px;font-size:34px;font-weight:700;color:#fff}
.copy{left:0;top:2524px;width:1200px;height:70px;background:var(--footer-bottom);color:#ddd;font-size:12px;text-align:center;line-height:70px}
</style>
</head>
<body>

<svg width="0" height="0" style="position:absolute">
  <defs>
    <symbol id="i-user" viewBox="0 0 14 14"><circle cx="7" cy="4.5" r="3" fill="none" stroke="currentColor"/><path d="M1.5 13c0-3 2.5-4.5 5.5-4.5s5.5 1.5 5.5 4.5" fill="none" stroke="currentColor"/></symbol>
    <symbol id="i-cal" viewBox="0 0 14 14"><rect x="1" y="2.5" width="12" height="10" fill="none" stroke="currentColor"/><path d="M1 5.5h12" stroke="currentColor"/></symbol>
    <symbol id="i-chat" viewBox="0 0 14 14"><path d="M1 1.5h12v8H6l-3 3v-3H1z" fill="none" stroke="currentColor"/></symbol>
    <symbol id="i-star" viewBox="0 0 14 14"><path d="M7 1l1.8 3.8 4.2.5-3.1 2.9.8 4.1L7 10.3 3.3 12.3l.8-4.1L1 5.3l4.2-.5z" fill="none" stroke="currentColor"/></symbol>
    <symbol id="i-folder" viewBox="0 0 14 14"><path d="M1 3h4.5l1.2 1.5H13v7.5H1z" fill="none" stroke="currentColor"/></symbol>
  </defs>
</svg>

<header>
  <div class="abs topbar"></div>
  <div class="abs logo">Harlow Daily</div>
  <div class="abs account">LOGIN<span>|</span>REGISTER</div>
  <div class="abs social-mini"><i></i><i></i><i></i><i></i></div>
  <nav class="abs nav">
    <ul>
      <li class="active" style="left:0">Home</li>
      <li style="left:134px">About Us</li>
      <li style="left:293px">Services</li>
      <li style="left:440px">News</li>
      <li style="left:580px">Lifestyle</li>
      <li style="left:734px">Business</li>
      <li style="left:870px">Tech</li>
    </ul>
  </nav>
</header>

<section class="abs hero">
  <div class="photo" role="img" aria-label="Businessman holding a tablet, double exposure with a city skyline"></div>
  <h1 class="abs hero-title">HARLOW DAILY</h1>
  <p class="abs hero-sub">Neque porro quisquam est qui</p>
  <div class="abs hero-arrows">
    <span><svg width="12" height="12" viewBox="0 0 12 12"><path d="M8 2L4 6l4 4" stroke="#fff" stroke-width="2" fill="none"/></svg></span>
    <span><svg width="12" height="12" viewBox="0 0 12 12"><path d="M4 2l4 4-4 4" stroke="#fff" stroke-width="2" fill="none"/></svg></span>
  </div>
</section>

<!-- Featured -->
<h2 class="abs heading" style="left:95px;top:734px">Featured</h2>
<div class="abs rule" style="left:92px;top:768px;width:690px"></div>
<section class="abs panel" style="left:92px;top:771px;width:690px;height:638px"></section>

<article class="card" style="left:116px;top:794px">
  <div style="position:absolute;inset:0;background:linear-gradient(135deg,#b8c4cf,#3b4a5a 60%,#1e2733)" role="img" aria-label="Business colleagues laughing in an office"></div>
  <div class="shade"></div><h3>Neque porro quisquam est</h3>
  <div class="meta"><span><svg class="ico"><use href="#i-folder"/></svg> News</span><span class="icons"><svg class="ico"><use href="#i-user"/></svg><svg class="ico"><use href="#i-cal"/></svg><svg class="ico"><use href="#i-chat"/></svg></span></div>
</article>
<article class="card" style="left:450px;top:794px">
  <div style="position:absolute;inset:0;background:linear-gradient(135deg,#7f8a94,#3d4650 60%,#20262d)" role="img" aria-label="Smiling man in a business suit"></div>
  <div class="shade"></div><h3>Neque porro quisquam est</h3>
  <div class="meta"><span><svg class="ico"><use href="#i-folder"/></svg> Business , Seo</span><span class="icons"><svg class="ico"><use href="#i-user"/></svg><svg class="ico"><use href="#i-cal"/></svg><svg class="ico"><use href="#i-chat"/></svg></span></div>
</article>
<article class="card" style="left:116px;top:1101px">
  <div style="position:absolute;inset:0;background:linear-gradient(135deg,#6b5a4a,#3a3632 55%,#1c1b1a)" role="img" aria-label="Man in a white shirt standing in a workshop"></div>
  <div class="shade"></div><h3>Neque porro quisquam est</h3>
  <div class="meta"><span><svg class="ico"><use href="#i-folder"/></svg> Business</span><span class="icons"><svg class="ico"><use href="#i-user"/></svg><svg class="ico"><use href="#i-cal"/></svg></span></div>
</article>
<article class="card" style="left:450px;top:1101px">
  <div style="position:absolute;inset:0;background:linear-gradient(135deg,#a9c3d6,#5f7f98 55%,#2c3d4c)" role="img" aria-label="Team of colleagues working at a laptop"></div>
  <div class="badge"><b>10</b><small>Amazing</small></div>
  <div class="shade"></div><h3>Neque porro quisquam est</h3>
  <div class="meta"><span><svg class="ico"><use href="#i-folder"/></svg> Tech</span><span class="icons"><svg class="ico"><use href="#i-user"/></svg><svg class="ico"><use href="#i-cal"/></svg></span></div>
</article>

<!-- Popular posts -->
<h2 class="abs heading" style="left:800px;top:734px">Popular Posts</h2>
<div class="abs rule" style="left:797px;top:768px;width:313px"></div>
<section class="abs panel" style="left:797px;top:771px;width:313px;height:638px">
  <div class="pop-item" style="top:21px"><div class="thumb" style="background:linear-gradient(135deg,#c9dbe8,#6d8fab)" role="img" aria-label="Hands using a tablet"></div><div><p>Ipsum is simply dummy text of the printing and type</p><div class="mini-icons" style="color:#999"><svg><use href="#i-star"/></svg><svg><use href="#i-cal"/></svg><svg><use href="#i-user"/></svg></div></div></div>
  <div class="pop-item" style="top:116px"><div class="thumb" style="background:linear-gradient(135deg,#b6bcc3,#3f4852)" role="img" aria-label="Business handshake"></div><div><p>Ipsum is simply dummy text of the printing and type</p><div class="mini-icons" style="color:#999"><svg><use href="#i-star"/></svg><svg><use href="#i-cal"/></svg><svg><use href="#i-chat"/></svg></div></div></div>
  <div class="pop-item" style="top:211px"><div class="thumb" style="background:linear-gradient(135deg,#eef0f2,#9aa6b2)" role="img" aria-label="Bright office with desks"></div><div><p>Ipsum is simply dummy text of the printing and type</p><div class="mini-icons" style="color:#999"><svg><use href="#i-star"/></svg><svg><use href="#i-cal"/></svg><svg><use href="#i-user"/></svg></div></div></div>
  <div class="pop-item" style="top:307px"><div class="thumb" style="background:linear-gradient(135deg,#e4e6e8,#7a6c64)" role="img" aria-label="Businesswoman portrait"></div><div><p>Ipsum is simply dummy text of the printing and type</p><div class="mini-icons" style="color:#999"><svg><use href="#i-star"/></svg><svg><use href="#i-cal"/></svg><svg><use href="#i-user"/></svg></div></div></div>
  <div class="pop-item" style="top:407px"><div class="thumb" style="background:linear-gradient(135deg,#eceff2,#3a4450)" role="img" aria-label="Two businessmen standing"></div><div><p>Ipsum is simply dummy text of the printing and type</p><div class="mini-icons" style="color:#999"><svg><use href="#i-star"/></svg><svg><use href="#i-cal"/></svg><svg><use href="#i-user"/></svg></div></div></div>
  <div class="pop-item" style="top:507px"><div class="thumb" style="background:linear-gradient(135deg,#a5866b,#3c5a7a)" role="img" aria-label="Smiling man in a blue shirt"></div><div><p>Ipsum is simply dummy text of the printing and type</p><div class="mini-icons" style="color:#999"><svg><use href="#i-star"/></svg><svg><use href="#i-user"/></svg><svg><use href="#i-chat"/></svg></div></div></div>
</section>

<!-- Business -->
<h2 class="abs heading" style="left:90px;top:1458px">Business</h2>
<div class="abs" style="left:737px;top:1469px;display:flex;gap:5px"><i style="width:7px;height:7px;border-radius:50%;background:#ccc"></i><i style="width:7px;height:7px;border-radius:50%;background:#333"></i><i style="width:7px;height:7px;border-radius:50%;background:#ccc"></i></div>
<div class="abs rule" style="left:90px;top:1493px;width:692px"></div>
<section class="abs panel" style="left:90px;top:1496px;width:692px;height:311px">
  <div class="biz" style="left:24px"><div class="img" style="background:linear-gradient(135deg,#d7dde3,#5c6a78)" role="img" aria-label="Colleagues in a meeting room"></div><p>Ipsum is simply dummy text of the printing and type</p><div class="date"><svg class="ico" style="color:#999"><use href="#i-cal"/></svg>27 March, 2016</div></div>
  <div class="biz" style="left:243px"><div class="img" style="background:linear-gradient(135deg,#e9e1d6,#8c7563)" role="img" aria-label="Business team around a table"></div><p>Ipsum is simply dummy text of the printing and type</p><div class="date"><svg class="ico" style="color:#999"><use href="#i-cal"/></svg>7 March, 2016</div></div>
  <div class="biz" style="left:465px"><div class="img" style="background:linear-gradient(135deg,#a9c4da,#3e5f7e)" role="img" aria-label="Handshake in front of a city skyline"></div><p>Ipsum is simply dummy text of the printing and type</p><div class="date"><svg class="ico" style="color:#999"><use href="#i-cal"/></svg>1 January, 2016</div></div>
</section>

<!-- Tech -->
<h2 class="abs heading" style="left:800px;top:1458px">Tech</h2>
<svg class="abs" style="left:1086px;top:1464px" width="20" height="14" viewBox="0 0 20 14"><path d="M7 2L2 7l5 5M13 2l5 5-5 5" stroke="#333" stroke-width="1.6" fill="none"/></svg>
<div class="abs rule" style="left:797px;top:1493px;width:313px"></div>
<section class="abs panel" style="left:797px;top:1496px;width:313px;height:311px">
  <div class="card" style="left:20px;top:19px;width:273px;height:268px">
    <div style="position:absolute;inset:0;background:linear-gradient(135deg,#b9d3e6,#5b86a7 55%,#233a52)" role="img" aria-label="Laptop on a desk with glowing network lines"></div>
    <div class="shade"></div><h3 style="font-size:16px;left:20px">Porro quisquam est, qui sum</h3>
    <div class="meta" style="left:20px;right:16px"><span><svg class="ico"><use href="#i-folder"/></svg> Photography</span><span class="icons"><svg class="ico"><use href="#i-user"/></svg><svg class="ico"><use href="#i-cal"/></svg><svg class="ico"><use href="#i-chat"/></svg></span></div>
  </div>
</section>

<!-- News -->
<h2 class="abs heading" style="left:88px;top:1831px">News</h2>
<div class="abs rule" style="left:90px;top:1866px;width:692px"></div>
<section class="abs panel" style="left:90px;top:1869px;width:692px;height:375px">
  <div class="card" style="left:19px;top:40px;width:316px;height:295px">
    <div style="position:absolute;inset:0;background:linear-gradient(135deg,#c9b9a8,#6d6a6e 50%,#2a3340)" role="img" aria-label="Businessman with rising chart overlay"></div>
    <div class="badge"><b>8.7</b><small>Awesome</small></div>
    <div class="shade"></div><h3 style="left:22px">Interview with mara ellison</h3>
    <div class="meta"><span><svg class="ico"><use href="#i-folder"/></svg> Interview</span><span class="icons"><svg class="ico"><use href="#i-user"/></svg><svg class="ico"><use href="#i-cal"/></svg><svg class="ico"><use href="#i-chat"/></svg></span></div>
  </div>
  <div class="pop-item list-item" style="left:359px;top:40px"><div class="thumb" style="width:81px;height:81px;background:linear-gradient(135deg,#dfe5ea,#4a5866)" role="img" aria-label="Businessman at a window"></div><div><p>Ipsum is simply dummy text of the printing and type</p><div class="mini-icons" style="color:#999"><svg><use href="#i-star"/></svg><svg><use href="#i-cal"/></svg><svg><use href="#i-user"/></svg><svg><use href="#i-chat"/></svg></div></div></div>
  <div class="pop-item list-item" style="left:359px;top:142px"><div class="thumb" style="width:81px;height:81px;background:linear-gradient(135deg,#f0e6dc,#9a7a66)" role="img" aria-label="Colleagues reviewing documents"></div><div><p>Ipsum is simply dummy text of the printing and type</p><div class="mini-icons" style="color:#999"><svg><use href="#i-cal"/></svg><svg><use href="#i-user"/></svg><svg><use href="#i-chat"/></svg></div></div></div>
  <div class="pop-item list-item" style="left:359px;top:244px"><div class="thumb" style="width:81px;height:81px;background:linear-gradient(135deg,#dce6ef,#2f4a6a)" role="img" aria-label="Businessman in a suit"></div><div><p>Ipsum is simply dummy text of the printing and type</p><div class="mini-icons" style="color:#999"><svg><use href="#i-star"/></svg><svg><use href="#i-cal"/></svg><svg><use href="#i-user"/></svg><svg><use href="#i-chat"/></svg></div></div></div>
</section>

<!-- Tags -->
<h2 class="abs heading" style="left:800px;top:1831px">Tags</h2>
<div class="abs rule" style="left:797px;top:1866px;width:313px"></div>
<section class="abs panel" style="left:797px;top:1869px;width:313px;height:244px">
  <span class="tag" style="left:20px;top:23px;width:102px">News</span>
  <span class="tag" style="left:128px;top:23px;width:97px">business</span>
  <span class="tag" style="left:20px;top:64px;width:114px">Lifestyle</span>
  <span class="tag" style="left:138px;top:64px;width:156px">sitepress themes</span>
  <span class="tag" style="left:20px;top:105px;width:74px">Travel</span>
  <span class="tag" style="left:104px;top:105px;width:145px">portfolio carousel</span>
  <span class="tag on" style="left:20px;top:146px;width:112px">Tech</span>
  <span class="tag" style="left:136px;top:146px;width:152px">sitepress plugins</span>
  <span class="tag" style="left:20px;top:187px;width:156px">begginers tutorials</span>
</section>

<div class="count" style="left:799px;background:var(--fans)"><i></i>259<br>fans</div>
<div class="count" style="left:906px;background:var(--followers)"><i></i>568<br>followers</div>
<div class="count" style="left:1013px;background:var(--subs)"><i></i>101<br>subscribers</div>

<!-- Footer -->
<footer class="abs footer">
  <h4 style="left:93px">Newsletters Sign Up</h4>
  <p class="abs" style="left:93px;top:70px;width:230px;line-height:17px">Sign up for our daily email by entering your information below</p>
  <div class="email">Email address</div>
  <div class="subscribe">SUBSCRIBE</div>

  <h4 style="left:405px">Get In Touch</h4>
  <p class="abs" style="left:405px;top:80px">Address : 14 Fenwick St, Eastgate<br>Norwick, NW4 2LP</p>
  <p class="abs" style="left:405px;top:145px">Phone : 0123 456789</p>
  <p class="abs" style="left:405px;top:178px">Email : hello@harlowdaily.test</p>

  <h4 style="left:683px">Follow Us On</h4>
  <div class="follow" style="top:76px"><i></i>Pagewall</div>
  <div class="follow" style="top:119px"><i></i>Chirpline</div>
  <div class="follow" style="top:162px"><i></i>Snapgrid</div>

  <div class="abs foot-logo">Harlow Daily</div>
</footer>
<div class="abs copy">Copyright © 2016. All Rights Reserved</div>

</body>
</html>
```